Dovecote Realty

Business cards for 4 people

They need to say for all
87 Tarrow Quay, Boston MA 02114

Each person will have their own personal information
We would like gold embossing for the name of the company
Marla is the blonde sitting in the chair smiling her information should be on the back of the card with her name and information
Should say for slogan classic pattern, elevated experience
marla@dovecoteprops.com
(413) 555-0182

Odette is the brunette with wavy hair in the tan suit celina@dovecoteprops.com
(617) 555-0137

faith@dovecoteprops.com
(413) 555-0164
standing next to the chair

hope@dovecoteprops.com
(413) 555-0199
close up headshot

```html
<!DOCTYPE html>
<html lang="en">
<head>
<meta charset="utf-8">
<title>Dovecote Realty Business Card</title>
<link href="https://fonts.googleapis.com/css2?family=Montserrat:wght@400;500;700&display=swap" rel="stylesheet">
<style>
  :root {
    --bg: #e4e4e4;
    --navy: #22304f;
    --navy-light: #6b7a92;
    --navy-mid: #4a5a76;
    --gold: #d8aa5e;
    --gold-light: #e8c48c;
    --white: #ffffff;
    --photo-light: #ecebea;
    --photo-dark: #3e3230;
  }
  * { margin: 0; padding: 0; box-sizing: border-box; }
  html, body { width: 1200px; height: 1200px; overflow: hidden; }
  body {
    background: var(--bg);
    font-family: "Montserrat", sans-serif;
    position: relative;
  }
  .card {
    position: absolute;
    left: 180px;
    width: 840px;
    height: 480px;
    border-radius: 26px;
    overflow: hidden;
    box-shadow: 0 10px 28px rgba(0,0,0,0.18);
  }
  .card-front {
    top: 90px;
    background: linear-gradient(100deg, var(--navy-light) 0%, var(--navy-mid) 35%, var(--navy) 70%);
  }
  .card-back { top: 630px; }
  .card-back .card-shapes { position: absolute; inset: 0; }

  .brand {
    position: absolute;
    display: flex;
    align-items: center;
    gap: 18px;
  }
  .brand-mark {
    width: 34px; height: 34px;
    border-radius: 50%;
    border: 3px solid currentColor;
    flex: none;
  }
  .brand-name {
    font-weight: 500;
    letter-spacing: 0.18em;
    text-transform: uppercase;
    white-space: nowrap;
  }
  .brand-front {
    color: var(--gold);
    left: 50%; top: 50%;
    transform: translate(-50%, -50%);
  }
  .brand-front .brand-name { font-size: 44px; }
  .brand-front .brand-mark { width: 46px; height: 46px; }

  .brand-back {
    color: var(--navy);
    right: 50px; top: 370px;
  }
  .brand-back .brand-name { font-size: 25px; }

  .person {
    position: absolute;
    left: 62px; top: 150px;
    color: var(--white);
  }
  .person-name { font-size: 38px; font-weight: 700; line-height: 1.1; }
  .person-title { font-size: 21px; font-weight: 400; margin-top: 8px; }

  .portrait {
    position: absolute;
    left: 620px; top: 48px;
    width: 176px; height: 176px;
    border-radius: 50%;
    background: linear-gradient(180deg, var(--photo-light) 0%, var(--photo-light) 30%, var(--photo-dark) 100%);
  }

  .contact {
    position: absolute;
    left: 62px; top: 318px;
    color: var(--white);
    font-size: 20px;
    line-height: 1.3;
  }
  .contact-address { margin-bottom: 10px; }
  .contact-list { list-style: none; }
  .contact-list li { display: flex; align-items: center; gap: 12px; height: 28px; }
  .contact-list svg { width: 20px; height: 20px; fill: var(--navy); flex: none; }
</style>
</head>
<body>

  <section class="card card-front" aria-label="Card front">
    <div class="brand brand-front">
      <span class="brand-mark"></span>
      <span class="brand-name">Dovecote Realty</span>
    </div>
  </section>

  <section class="card card-back" aria-label="Card back">
    <svg class="card-shapes" viewBox="0 0 840 480" preserveAspectRatio="none">
      <defs>
        <linearGradient id="navyFade" x1="0" y1="0" x2="1" y2="0.3">
          <stop offset="0" stop-color="#6b7a92"/>
          <stop offset="0.45" stop-color="#2e3c5b"/>
          <stop offset="1" stop-color="#22304f"/>
        </linearGradient>
        <linearGradient id="goldFade" x1="0" y1="0" x2="1" y2="0">
          <stop offset="0" stop-color="#e8c48c"/>
          <stop offset="0.5" stop-color="#dcae66"/>
          <stop offset="1" stop-color="#d8aa5e"/>
        </linearGradient>
      </defs>
      <rect width="840" height="480" fill="url(#navyFade)"/>
      <path d="M0 290 L370 290 L425 318 L840 318 L840 480 L0 480 Z" fill="url(#goldFade)"/>
    </svg>

    <div class="portrait" role="img" aria-label="Portrait photo of Marla Hale"></div>

    <div class="person">
      <h1 class="person-name">Marla Hale</h1>
      <p class="person-title">Founder &amp; Director</p>
    </div>

    <div class="contact">
      <p class="contact-address">87 Tarrow Quay, Boston,<br>MA 02114, United States</p>
      <ul class="contact-list">
        <li>
          <svg viewBox="0 0 24 24"><path d="M6.6 10.8a15 15 0 0 0 6.6 6.6l2.2-2.2a1 1 0 0 1 1-.25 11.4 11.4 0 0 0 3.6.57 1 1 0 0 1 1 1V20a1 1 0 0 1-1 1A17 17 0 0 1 3 4a1 1 0 0 1 1-1h3.5a1 1 0 0 1 1 1c0 1.25.2 2.45.57 3.57a1 1 0 0 1-.25 1z"/></svg>
          <span>(413)555-0182</span>
        </li>
        <li>
          <svg viewBox="0 0 24 24"><path d="M2 5h20v2l-10 7L2 7z M2 9l10 7 10-7v10H2z"/></svg>
          <span>marla@dovecoteprops.com</span>
        </li>
        <li>
          <svg viewBox="0 0 24 24"><path d="M12 2a10 10 0 1 0 0 20 10 10 0 0 0 0-20zm6.9 6h-2.9a15 15 0 0 0-1.4-3.6A8 8 0 0 1 18.9 8zM12 4c.8 1.2 1.5 2.5 1.9 4h-3.8c.4-1.5 1.1-2.8 1.9-4zM4.3 14a8 8 0 0 1 0-4h3.4a16 16 0 0 0 0 4zm.8 2h2.9c.3 1.3.8 2.5 1.4 3.6A8 8 0 0 1 5.1 16zM8 8H5.1a8 8 0 0 1 4.3-3.6C8.8 5.5 8.3 6.7 8 8zm4 12c-.8-1.2-1.5-2.5-1.900-4h3.8c-.4 1.5-1.1 2.8-1.9 4zm2.3-6H9.7a14 14 0 0 1 0-4h4.6a14 14 0 0 1 0 4zm.3 5.6c.6-1.1 1.1-2.3 1.4-3.6h2.9a8 8 0 0 1-4.3 3.6zm1.7-5.6a16 16 0 0 0 0-4h3.4a8 8 0 0 1 0 4z"/></svg>
          <span>www.dovecoteprops.com</span>
        </li>
      </ul>
    </div>

    <div class="brand brand-back">
      <span class="brand-mark"></span>
      <span class="brand-name">Dovecote Realty</span>
    </div>
  </section>

</body>
</html>
```